Verdano Tiling Solutions, QBCC 4870312, ABN 28459106783, Email verdanotiling@tilebox-mail.com,Mobile 04159326

Verdano Tiling Solutions, is the name of my wall and floor tiling company and the details above are needed on the business card. Im open to see what people come up with i really have no colour requirements or other design specs as long as its not too plain.

```html
<!DOCTYPE html>
<html lang="en">
<head>
<meta charset="utf-8">
<title>Verdano Tiling Solutions – Business Card</title>
<link rel="stylesheet" href="https://fonts.googleapis.com/css2?family=Open+Sans:wght@300;400;600&display=swap">
<style>
  :root {
    --stage: #a9a9a9;
    --paper: #ffffff;
    --charcoal: #2b2b2b;
    --orange: #e8761f;
    --orange-deep: #d9601a;
    --red: #d0161d;
    --ink: #3a3a3a;
    --shadow: rgba(0, 0, 0, 0.28);
  }
  * { box-sizing: border-box; margin: 0; padding: 0; }
  html, body {
    width: 805px;
    height: 1200px;
    overflow: hidden;
    background: var(--stage);
    font-family: "Open Sans", sans-serif;
  }
  .stage {
    position: relative;
    width: 805px;
    height: 1200px;
  }
  .card {
    position: absolute;
    left: 102px;
    width: 600px;
    height: 343px;
    background: var(--paper);
    overflow: hidden;
    box-shadow: 0 10px 28px var(--shadow);
  }
  .card--front { top: 150px; }
  .card--back { top: 680px; }

  /* Front */
  .front__band {
    position: absolute;
    left: 0;
    width: 100%;
    background: var(--charcoal);
  }
  .front__band--top { top: 0; height: 98px; }
  .front__band--bottom { bottom: 0; height: 98px; }
  .front__accent {
    position: absolute;
    height: 26px;
  }
  .front__accent--orange-top { left: 0; top: 86px; width: 250px; background: var(--orange); }
  .front__accent--red-top { right: 0; top: 92px; width: 170px; height: 14px; background: var(--red); }
  .front__accent--orange-bottom { right: 0; bottom: 86px; width: 250px; background: var(--orange); }
  .front__accent--red-bottom { left: 0; bottom: 92px; width: 170px; height: 14px; background: var(--red); }
  .front__brand {
    position: absolute;
    left: 0;
    right: 0;
    top: 126px;
    height: 92px;
    display: flex;
    align-items: center;
    justify-content: center;
    gap: 14px;
  }
  .brand__square {
    width: 30px;
    height: 30px;
    background: var(--orange);
  }
  .brand__name {
    font-weight: 400;
    font-size: 30px;
    color: var(--ink);
    letter-spacing: 0.3px;
  }

  /* Back */
  .back__identity {
    position: absolute;
    left: 0;
    top: 0;
    width: 222px;
    height: 100%;
    padding: 0 18px 34px 26px;
    display: flex;
    flex-direction: column;
    justify-content: flex-end;
    gap: 14px;
  }
  .back__identity .brand__square { width: 34px; height: 34px; }
  .back__identity .brand__name {
    font-size: 25px;
    line-height: 1.15;
  }
  .back__stripe {
    position: absolute;
    top: 0;
    height: 100%;
  }
  .back__stripe--red-left { left: 222px; width: 12px; background: var(--red); }
  .back__stripe--dark-left { left: 234px; width: 8px; background: var(--charcoal); }
  .back__stripe--dark-right { right: 22px; width: 8px; background: var(--charcoal); }
  .back__stripe--red-right { right: 8px; width: 14px; background: var(--red); }
  .back__panel {
    position: absolute;
    top: 0;
    left: 242px;
    right: 30px;
    height: 100%;
    background: radial-gradient(circle at 40% 45%, var(--orange) 0%, var(--orange-deep) 100%);
    color: var(--paper);
    padding: 30px 26px 28px 30px;
    display: flex;
    flex-direction: column;
    justify-content: space-between;
    align-items: flex-end;
    text-align: right;
  }
  .person__name {
    font-size: 19px;
    font-weight: 400;
    letter-spacing: 2px;
    text-transform: uppercase;
  }
  .person__title {
    font-size: 10px;
    font-weight: 300;
    letter-spacing: 1.6px;
    text-transform: uppercase;
    margin-top: 4px;
  }
  .contacts {
    list-style: none;
    display: flex;
    flex-direction: column;
    gap: 7px;
  }
  .contacts__item {
    display: flex;
    align-items: center;
    justify-content: flex-end;
    gap: 10px;
    font-size: 11px;
    font-weight: 400;
    letter-spacing: 0.3px;
  }
  .contacts__icon {
    width: 18px;
    height: 18px;
    background: var(--paper);
    border-radius: 3px;
    display: flex;
    align-items: center;
    justify-content: center;
  }
  .contacts__icon svg { width: 12px; height: 12px; }
</style>
</head>
<body>
<main class="stage">

  <section class="card card--front" aria-label="Business card front">
    <div class="front__band front__band--top"></div>
    <div class="front__band front__band--bottom"></div>
    <div class="front__accent front__accent--orange-top"></div>
    <div class="front__accent front__accent--red-top"></div>
    <div class="front__accent front__accent--orange-bottom"></div>
    <div class="front__accent front__accent--red-bottom"></div>
    <div class="front__brand">
      <span class="brand__square"></span>
      <span class="brand__name">Verdano Tiling Solutions</span>
    </div>
  </section>

  <section class="card card--back" aria-label="Business card back">
    <div class="back__identity">
      <span class="brand__square"></span>
      <span class="brand__name">Verdano Tiling<br>Solutions</span>
    </div>
    <div class="back__stripe back__stripe--red-left"></div>
    <div class="back__stripe back__stripe--dark-left"></div>
    <div class="back__panel">
      <header class="person">
        <h1 class="person__name">Daniel Reyes</h1>
        <p class="person__title">General Manager</p>
      </header>
      <ul class="contacts">
        <li class="contacts__item">Mob 04159326
          <span class="contacts__icon">
            <svg viewBox="0 0 24 24"><path fill="#d9601a" d="M6.6 10.8a15.1 15.1 0 0 0 6.6 6.6l2.2-2.2c.3-.3.7-.4 1-.2 1.1.4 2.3.6 3.6.6.6 0 1 .4 1 1V20c0 .6-.4 1-1 1A17 17 0 0 1 3 4c0-.6.4-1 1-1h3.5c.6 0 1 .4 1 1 0 1.3.2 2.5.6 3.6.1.3 0 .7-.2 1z"/></svg>
          </span>
        </li>
        <li class="contacts__item">QBCC 4870312
          <span class="contacts__icon">
            <svg viewBox="0 0 24 24"><path fill="none" stroke="#d9601a" stroke-width="3" d="M4 12l5 5L20 6"/></svg>
          </span>
        </li>
        <li class="contacts__item">ABN 28459106783
          <span class="contacts__icon">
            <svg viewBox="0 0 24 24"><path fill="none" stroke="#d9601a" stroke-width="3" d="M4 12l5 5L20 6"/></svg>
          </span>
        </li>
        <li class="contacts__item">verdanotiling@tilebox-mail.com
          <span class="contacts__icon">
            <svg viewBox="0 0 24 24"><rect x="2" y="5" width="20" height="14" fill="none" stroke="#d9601a" stroke-width="2.4"/><path fill="none" stroke="#d9601a" stroke-width="2.4" d="M2 6l10 7 10-7"/></svg>
          </span>
        </li>
        <li class="contacts__item">Wall and Floor Tiling
          <span class="contacts__icon">
            <svg viewBox="0 0 24 24"><path fill="#d9601a" d="M12 2a7 7 0 0 0-7 7c0 5 7 13 7 13s7-8 7-13a7 7 0 0 0-7-7zm0 9.5a2.5 2.5 0 1 1 0-5 2.5 2.5 0 0 1 0 5z"/></svg>
          </span>
        </li>
      </ul>
    </div>
    <div class="back__stripe back__stripe--dark-right"></div>
    <div class="back__stripe back__stripe--red-right"></div>
  </section>

</main>
</body>
</html>
```